Tampa Bay fishing guide needs stunning website.

I currently have a site - www.reelcoveguide.net which I personally put together using the Pagely platform and I am looking for a redesign on a different platform (Sitecraft?) that will allow me to easily create landing pages in the future. Would like to have a block for visitors to opt in to newsletter. Need social media links on all pages.

I would like to let my visitors know that I am able to handle their fishing charter needs here in the Tampa Bay area, if I'm not available for the dates they are looking to go I can refer them to a reputable captain in the area.

Target Market(s)

United States

Industry/Entity Type

Tourism

Coding

Coded - Design and coding required

Number of Pages Required

5+ page

Font styles to use
Sans Serif

Colors
0355a3
3176b5
85abd2
fbf289

Requirements
Must have
• Mobile Responsive, Ability to insert Vantor Metrics, Chatterbox pixels, ability to add custom landing pages in future
Nice to have
• Clean, easy navigation

```html
<!DOCTYPE html>
<html lang="en">
<head>
<meta charset="utf-8">
<title>Capt. Wade Harlan – Tampa Bay Fishing Charters</title>
<link href="https://fonts.googleapis.com/css2?family=Roboto:wght@400;500;700&family=Merriweather:ital@1&display=swap" rel="stylesheet">
<style>
  :root{
    --navy:#0355a3;
    --blue:#3176b5;
    --sky:#85abd2;
    --sun:#fbf289;
    --ink:#2b2b2b;
    --muted:#777;
    --grey-btn:#7d7d7d;
    --band:#ececec;
    --white:#fff;
  }
  *{margin:0;padding:0;box-sizing:border-box}
  html,body{width:1200px;height:2521px;overflow:hidden}
  body{position:relative;background:var(--white);font-family:"Roboto",Arial,sans-serif;color:var(--ink)}
  .abs{position:absolute}

  /* hero */
  .hero{left:0;top:0;width:1200px;height:595px;
    background:radial-gradient(ellipse at 60% 55%,#5c7fa8 0%,#1d3550 30%,#0b1a26 60%,#070f16 100%)}
  .site-header{left:0;top:0;width:1200px;height:107px;border-bottom:1px solid rgba(255,255,255,.12)}
  .brand{left:75px;top:34px;display:flex;align-items:center;gap:10px;color:var(--blue);font-weight:700;font-size:24px;letter-spacing:.3px}
  .brand-dot{width:14px;height:14px;border-radius:50%;background:var(--blue)}
  .header-rule{left:296px;top:25px;width:1px;height:58px;background:rgba(255,255,255,.2)}
  .main-nav{top:52px;font-size:13px;font-weight:500;color:var(--white);text-transform:uppercase}
  .main-nav.active{color:var(--sun)}
  .social{display:flex;gap:18px}
  .social span{width:22px;height:22px;border:2px solid var(--sun);border-radius:50%}
  .site-header .social{left:1020px;top:48px}

  /* intro */
  .intro{left:74px;top:561px;width:1052px;height:252px;background:var(--sun);text-align:center;padding:42px 70px 0}
  .intro h1{font-size:25px;font-weight:500;line-height:34px;color:var(--ink);text-transform:uppercase;padding:0 180px}
  .intro p{margin-top:26px;font-size:12.5px;line-height:22px;color:#8a8a6a}

  /* features */
  .feature{top:890px;width:330px;height:120px}
  .feature-icon{left:0;top:0;width:64px;height:64px;border-radius:50%;background:var(--blue);display:flex;align-items:center;justify-content:center}
  .feature h3{position:absolute;left:88px;top:0;font-size:18px;font-weight:500}
  .feature p{position:absolute;left:88px;top:36px;width:240px;font-size:12.5px;line-height:22px;color:var(--muted)}
  .btn{display:flex;align-items:center;justify-content:center;color:var(--white);font-size:12px;font-weight:700;text-transform:uppercase;letter-spacing:.3px}
  .btn-primary{background:var(--blue)}
  .btn-grey{background:var(--grey-btn)}

  /* tournaments */
  .tournaments{left:0;top:1144px;width:1200px;height:553px;background:linear-gradient(135deg,#f2f2f2,#e4e4e4 50%,#f0f0f0)}
  .section-title{font-size:22px;font-weight:700;color:var(--ink);text-transform:uppercase;left:77px}
  .event{top:1273px;width:326px;text-align:center}
  .event-photo{width:326px;height:188px;border:3px solid var(--white)}
  .event h4{margin-top:36px;font-size:18px;font-weight:500;color:var(--blue)}
  .event p{margin-top:10px;font-size:12.5px;line-height:19px;color:var(--muted);padding:0 18px}
  .event .btn{margin:16px auto 0;width:121px;height:42px;font-size:11.5px}

  /* testimonials */
  .testimonials{left:0;top:1697px;width:1200px;height:494px;background:linear-gradient(#fff,#e8e8e8)}
  .quote{top:1835px;width:328px;height:155px;background:var(--white);padding:22px 24px 0 70px}
  .quote-mark{position:absolute;left:24px;top:14px;font-size:52px;line-height:1;font-weight:700;color:var(--blue);font-family:Georgia,serif}
  .quote p{font-size:12.5px;line-height:22px;color:var(--muted);font-style:italic;text-align:justify}
  .quote-tail{position:absolute;left:200px;bottom:-24px}
  .avatar{top:2004px;width:77px;height:77px;border-radius:50%;background:radial-gradient(circle,#d9b394,#9a7257)}
  .author{top:2096px;width:100px;text-align:center;font-size:14px;font-weight:500;color:var(--blue)}

  /* newsletter */
  .newsletter{left:0;top:2191px;width:1200px;height:225px;background:linear-gradient(#3176b5,#1d62a8)}
  .newsletter h2{position:absolute;left:0;width:1200px;top:52px;text-align:center;font-family:"Merriweather",Georgia,serif;font-style:italic;font-weight:400;font-size:28px;color:var(--white)}
  .signup-field{left:349px;top:122px;width:373px;height:47px;background:var(--white);display:flex;align-items:center;gap:12px;padding-left:18px;font-size:13px;color:#aaa;font-style:italic}
  .signup-btn{left:722px;top:122px;width:128px;height:47px;background:var(--sky);font-size:14px}

  /* footer */
  .site-footer{left:0;top:2416px;width:1200px;height:105px;background:#1a5ea5;border-top:1px solid rgba(255,255,255,.15)}
  .footer-nav{left:77px;top:36px;display:flex;gap:14px;font-size:13px;color:var(--white)}
  .footer-nav .sep{color:rgba(255,255,255,.7)}
  .copyright{left:77px;top:58px;font-size:12.5px;color:var(--white)}
  .site-footer .social{left:1005px;top:36px}
  .site-footer .social span{border-color:var(--white)}
</style>
</head>
<body>

<section class="abs hero" role="img" aria-label="Photograph of a smiling angler on a boat holding a rod while a tarpon leaps from dark water"></section>

<header class="abs site-header">
  <div class="abs brand"><span class="brand-dot"></span>Capt. Wade Harlan</div>
  <div class="abs header-rule"></div>
  <nav>
    <span class="abs main-nav active" style="left:341px">Home</span>
    <span class="abs main-nav" style="left:418px">About Us</span>
    <span class="abs main-nav" style="left:519px">Pick Up Locations</span>
    <span class="abs main-nav" style="left:682px">Rates</span>
    <span class="abs main-nav" style="left:763px">Contact Us</span>
    <span class="abs main-nav" style="left:879px">Gift Card</span>
  </nav>
  <div class="abs social" aria-label="Social links"><span></span><span></span><span></span></div>
</header>

<section class="abs intro">
  <h1>Tampa Bay, Fishing Guide, Tampa Bay Fishing Charters</h1>
  <p>Capt. Wade Harlan, with over 20 years' experience, Native fishing charter tampa charter captain offering full and half day fishing charters on the waters of Tampa Bay. If you're looking for a great fishing charter tampa don't hesitate to contact Capt. Wade or you can simply book your trip online here. Come enjoy a wonderful day fishing charters Tampa for Tarpon, Snook, Redfish, Trout, Sharks, Cobia, Spanish mackerel</p>
</section>

<div class="abs feature" style="left:76px">
  <div class="abs feature-icon">
    <svg width="30" height="30" viewBox="0 0 30 30"><circle cx="15" cy="15" r="13" fill="#fff"/><circle cx="15" cy="9" r="2" fill="#3176b5"/><rect x="13.2" y="12.5" width="3.6" height="10" fill="#3176b5"/></svg>
  </div>
  <h3>Shortly About Us</h3>
  <p>Aenean vitae fermentum mauris. Sed sollicitudin in nisi sit amet hendrerit. Vestibulum ante ipsum prim</p>
</div>
<div class="abs feature" style="left:442px">
  <div class="abs feature-icon">
    <svg width="30" height="30" viewBox="0 0 30 30" fill="#fff"><path d="M8 4h14v6a7 7 0 0 1-14 0z"/><path d="M8 6H3v3a5 5 0 0 0 5 5M22 6h5v3a5 5 0 0 1-5 5" fill="none" stroke="#fff" stroke-width="2"/><rect x="13" y="16" width="4" height="6"/><rect x="9" y="22" width="12" height="4"/></svg>
  </div>
  <h3>Our Awards</h3>
  <p>Aenean vitae fermentum mauris. Sed sollicitudin in nisi sit amet hendrerit. Vestibulum ante ipsum prim</p>
</div>
<div class="abs feature" style="left:808px">
  <div class="abs feature-icon">
    <svg width="32" height="30" viewBox="0 0 32 30" fill="#fff"><circle cx="16" cy="9" r="5"/><path d="M7 25a9 9 0 0 1 18 0z"/><circle cx="6" cy="12" r="3.5"/><circle cx="26" cy="12" r="3.5"/><path d="M0 24a6 6 0 0 1 8-5.5 11 11 0 0 0-2 5.5zM32 24a6 6 0 0 0-8-5.5 11 11 0 0 1 2 5.5z"/></svg>
  </div>
  <h3>Our Community</h3>
  <p>Aenean vitae fermentum mauris. Sed sollicitudin in nisi sit amet hendrerit. Vestibulum ante ipsum prim</p>
</div>

<a class="abs btn btn-primary" style="left:435px;top:1043px;width:154px;height:46px">View All</a>
<a class="abs btn btn-grey" style="left:613px;top:1043px;width:154px;height:46px">Contact Us</a>

<section class="abs tournaments"></section>
<h2 class="abs section-title" style="top:1214px">Latest Tournaments</h2>

<article class="abs event" style="left:77px">
  <div class="event-photo" role="img" aria-label="Photograph of anglers on a boat landing a large snook over green water" style="background:linear-gradient(135deg,#1c7a72,#3d8f86 50%,#d8d8d8)"></div>
  <h4>Mauris Tincidunt</h4>
  <p>Aenean vitae fermentum mauris. Sed sollicitudin in nisi sit amet hendrerit. Vestibulum ante</p>
  <a class="btn btn-primary">Details</a>
</article>
<article class="abs event" style="left:438px">
  <div class="event-photo" role="img" aria-label="Photograph of a couple holding up a large snook under blue sky" style="background:linear-gradient(#4e88c6,#8cb4d8 55%,#7a6a50)"></div>
  <h4>Donec dictum</h4>
  <p>Aenean vitae fermentum mauris. Sed sollicitudin in nisi sit amet hendrerit. Vestibulum ante</p>
  <a class="btn btn-primary">Details</a>
</article>
<article class="abs event" style="left:798px">
  <div class="event-photo" role="img" aria-label="Photograph of a young angler holding a snook on the water" style="background:linear-gradient(135deg,#3b5f93,#8da9c9 50%,#e9e9e9)"></div>
  <h4>Pellentesque eu</h4>
  <p>Aenean vitae fermentum mauris. Sed sollicitudin in nisi sit amet hendrerit. Vestibulum ante</p>
  <a class="btn btn-primary">Details</a>
</article>

<section class="abs testimonials"></section>
<h2 class="abs section-title" style="top:1774px">Testimonial</h2>

<blockquote class="abs quote" style="left:76px">
  <span class="quote-mark">&ldquo;</span>
  <p>Pellentesque eu nulla sit amet elit porta ultricies a at ante. Praesent pulvinar maximus sapien ac commodo. Cras faucibus sit amet tortor quis</p>
  <svg class="quote-tail" width="26" height="24" viewBox="0 0 26 24"><path d="M0 0h26v24z" fill="#fff"/></svg>
</blockquote>
<blockquote class="abs quote" style="left:435px">
  <span class="quote-mark">&ldquo;</span>
  <p>Pellentesque eu nulla sit amet elit porta ultricies a at ante. Praesent pulvinar maximus sapien ac commodo. Cras faucibus sit amet tortor quis</p>
  <svg class="quote-tail" width="26" height="24" viewBox="0 0 26 24"><path d="M0 0h26v24z" fill="#fff"/></svg>
</blockquote>
<blockquote class="abs quote" style="left:796px">
  <span class="quote-mark">&ldquo;</span>
  <p>Pellentesque eu nulla sit amet elit porta ultricies a at ante. Praesent pulvinar maximus sapien ac commodo. Cras faucibus sit amet tortor quis</p>
  <svg class="quote-tail" width="26" height="24" viewBox="0 0 26 24"><path d="M0 0h26v24z" fill="#fff"/></svg>
</blockquote>

<div class="abs avatar" style="left:326px" role="img" aria-label="Portrait photo of the reviewer"></div>
<div class="abs avatar" style="left:687px" role="img" aria-label="Portrait photo of the reviewer"></div>
<div class="abs avatar" style="left:1047px" role="img" aria-label="Portrait photo of the reviewer"></div>
<span class="abs author" style="left:315px">Alan Doe</span>
<span class="abs author" style="left:675px">Alan Doe</span>
<span class="abs author" style="left:1036px">Alan Doe</span>

<section class="abs newsletter">
  <h2>Newsletter signup</h2>
  <div class="abs signup-field">
    <svg width="18" height="13" viewBox="0 0 18 13"><rect x="1" y="1" width="16" height="11" fill="none" stroke="#85abd2" stroke-width="1.4"/><path d="M1 1l8 6 8-6" fill="none" stroke="#85abd2" stroke-width="1.4"/></svg>
    Email Address
  </div>
  <a class="abs btn signup-btn">Send</a>
</section>

<footer class="abs site-footer">
  <nav class="abs footer-nav">
    <span>Homs</span><span class="sep">\</span>
    <span>About us</span><span class="sep">\</span>
    <span>Pick Up Location</span><span class="sep">\</span>
    <span>Rates</span><span class="sep">\</span>
    <span>Contact Us</span><span class="sep">\</span>
    <span>Gift Card</span>
  </nav>
  <p class="abs copyright">Copyright © 2016 Reel Cove Guide. All Right Reserved.</p>
  <div class="abs social" aria-label="Social links"><span></span><span></span><span></span></div>
</footer>

</body>
</html>
```